****Business Card Design for Quarrystone Development. Design based around attached logo/company name

I’m looking for business card design for my company Quarrystone Development Group,LLC. Design should be professional, sharp and minimal. Outside of the attached logos, greyscale colors for remainder of cards. My thoughts are two-sided card with attached logo on one side and my info on the other but open to one-sided as well with right design.
Target Market(s)
Real estate professionals including banks, private investors, property owners, developers, commercial tenants like Brewlantern, Grovika or Tanquist’s.
Industry/Entity Type
Commercial real estate development and investments.
Contact Information for Business Card
Name, title, email, phone #’s, web address and physical address
Font styles to use
Other font styles liked:
- Helvetica, Garamond, etc
Colors
Designer to choose only greyscale colors for use in the design.
Requirements
Must have
- Attached logo first or second options.
Nice to have
- Two sided card with logo on one side. Attached Logo/company name can be laid out any way that flows as long as it’s legible.name
Should not have
- No loud colors. ***Please do not include logo, I have removed the company design with a logo image.

```html
<!DOCTYPE html>
<html lang="en">
<head>
<meta charset="utf-8">
<title>Quarrystone Development Group, LLC — Business Cards</title>
<link rel="stylesheet" href="https://fonts.googleapis.com/css2?family=Cinzel:wght@400;700&family=Arimo:wght@400&display=swap">
<style>
  :root {
    --backdrop: #1f2023;
    --card: #5b6074;
    --ink: #ffffff;
    --ink-soft: #e3e5ec;
    --rule: rgba(255,255,255,0.55);
  }
  * { margin: 0; padding: 0; box-sizing: border-box; }
  html, body { width: 1200px; height: 852px; overflow: hidden; }
  body {
    background: var(--backdrop);
    position: relative;
    font-family: "Arimo", Helvetica, Arial, sans-serif;
    color: var(--ink);
  }
  .card {
    position: absolute;
    width: 540px;
    height: 309px;
    background: var(--card);
    box-shadow: 0 14px 30px rgba(0,0,0,0.55);
  }
  .card--front { left: 40px; top: 271px; }
  .card--back  { left: 620px; top: 271px; }

  .wordmark {
    position: absolute;
    font-family: "Cinzel", Garamond, serif;
    font-weight: 400;
    color: var(--ink);
    text-align: left;
    line-height: 1;
  }
  .wordmark__name { display: block; letter-spacing: 0.04em; }
  .wordmark__tag  { display: block; letter-spacing: 0.12em; }

  .card--front .wordmark { left: 118px; top: 122px; }
  .card--front .wordmark__name { font-size: 34px; }
  .card--front .wordmark__tag  { font-size: 13px; margin-top: 8px; }

  .card--back .wordmark { left: 30px; top: 185px; }
  .card--back .wordmark__name { font-size: 25px; }
  .card--back .wordmark__tag  { font-size: 9.5px; margin-top: 6px; }

  .divider {
    position: absolute;
    left: 280px; top: 60px;
    width: 1px; height: 190px;
    background: var(--rule);
  }
  .contact {
    position: absolute;
    left: 305px; top: 62px;
    font-size: 13px;
    line-height: 1.35;
    color: var(--ink-soft);
  }
  .contact__name {
    font-family: "Cinzel", Garamond, serif;
    font-weight: 700;
    font-size: 18px;
    color: var(--ink);
    letter-spacing: 0.03em;
  }
  .contact__title { margin-bottom: 18px; }
  .contact__address { margin-bottom: 14px; }
  .contact__line { display: flex; align-items: center; gap: 6px; }
  .contact__line svg { width: 11px; height: 11px; flex: none; }
</style>
</head>
<body>
  <section class="card card--front" aria-label="Card front">
    <div class="wordmark">
      <span class="wordmark__name">Quarrystone</span>
      <span class="wordmark__tag">Development Group, LLC</span>
    </div>
  </section>

  <section class="card card--back" aria-label="Card back">
    <div class="wordmark">
      <span class="wordmark__name">Quarrystone</span>
      <span class="wordmark__tag">Development Group, LLC</span>
    </div>
    <div class="divider"></div>
    <div class="contact">
      <div class="contact__name">Daniel Whitcombe</div>
      <div class="contact__title">Director</div>
      <div class="contact__address">1187 Fenwick Lane<br>Salem, OR 97304</div>
      <div class="contact__line">
        <svg viewBox="0 0 24 24" fill="currentColor"><path d="M6.6 10.8a15.1 15.1 0 0 0 6.6 6.6l2.2-2.2a1 1 0 0 1 1-.25 11.4 11.4 0 0 0 3.6.57 1 1 0 0 1 1 1V20a1 1 0 0 1-1 1A17 17 0 0 1 3 4a1 1 0 0 1 1-1h3.5a1 1 0 0 1 1 1c0 1.25.2 2.46.57 3.6a1 1 0 0 1-.25 1z"/></svg>
        <span>(555) 382-0147</span>
      </div>
      <div class="contact__line">
        <svg viewBox="0 0 24 24" fill="none" stroke="currentColor" stroke-width="2"><rect x="3" y="5" width="18" height="14"/><path d="M3 6l9 7 9-7"/></svg>
        <span>info@quarrystonegroup.com</span>
      </div>
      <div class="contact__line">
        <svg viewBox="0 0 24 24" fill="none" stroke="currentColor" stroke-width="2"><circle cx="12" cy="12" r="9"/><path d="M3 12h18M12 3c3 3 3 15 0 18M12 3c-3 3-3 15 0 18"/></svg>
        <span>www.quarrystonegroup.com</span>
      </div>
    </div>
  </section>
</body>
</html>
```